New Business Card Design Project

Need a design that will create an impact / strong impression towards our clients for our business. We are in the lighting business and we do lighting retrofits for large commercial to industrial clientele.

Target Market(s)

Lighting Industry

Industry/Entity Type

Business

Font styles to use
Other font styles liked:
• we would like to use the font on our logo, not sure what it is though..

Requirements
Must have
• Our logo.
Nice to have
• We are open to suggestions that have to do with lighting.

```html
<!DOCTYPE html>
<html lang="en">
<head>
<meta charset="utf-8">
<title>Brightline Retrofit Co. — Business Card</title>
<link href="https://fonts.googleapis.com/css2?family=Montserrat:wght@700&family=Open+Sans:wght@400;600&family=Roboto+Condensed:wght@700&display=swap" rel="stylesheet">
<style>
  :root {
    --stage: #2b2b2b;
    --paper: #f4f4f2;
    --green-light: #6cc24a;
    --green-mid: #12873c;
    --green-dark: #184f1c;
    --ink: #4a4a4a;
    --ink-dark: #1e5a22;
    --address-ink: #1d3d1d;
  }
  * { margin: 0; padding: 0; box-sizing: border-box; }
  html, body { width: 1200px; height: 886px; overflow: hidden; background: var(--stage); }
  .stage { position: relative; width: 1200px; height: 886px; }
  .card {
    position: absolute; width: 540px; height: 310px;
    background: var(--paper); border-radius: 18px; overflow: hidden;
  }
  .card--front { left: 80px; top: 90px; }
  .card--back { left: 580px; top: 486px; }
  .card svg.art { position: absolute; inset: 0; width: 540px; height: 310px; }

  .brand-name {
    font-family: "Montserrat", sans-serif; font-weight: 700;
    color: var(--green-dark); letter-spacing: 0.5px; white-space: nowrap;
  }
  .brand-rule { height: 2px; background: var(--green-mid); }
  .brand-mark { display: inline-block; width: 14px; height: 14px; background: var(--green-light); margin-left: 8px; vertical-align: middle; }

  .front-brand { position: absolute; left: 36px; top: 132px; }
  .front-brand .brand-name { font-size: 20px; }
  .front-brand .brand-rule { width: 230px; margin: 6px 0 5px; }
  .front-url { font-family: "Open Sans", sans-serif; font-size: 13px; color: var(--ink); }

  .back-brand { position: absolute; left: 30px; top: 70px; }
  .back-brand .brand-name { font-size: 18px; }
  .back-brand .brand-rule { width: 250px; margin: 6px 0 0; }

  .person { position: absolute; left: 230px; top: 30px; width: 160px; text-align: right; font-family: "Roboto Condensed", sans-serif; font-weight: 700; }
  .person-name { font-size: 19px; color: var(--ink-dark); }
  .person-title { font-size: 13px; color: var(--green-mid); }

  .contact { position: absolute; left: 30px; top: 122px; font-family: "Open Sans", sans-serif; color: var(--ink); }
  .contact-web { font-size: 13px; font-weight: 600; letter-spacing: 1.6px; line-height: 18px; }
  .contact-list { list-style: none; margin-top: 8px; }
  .contact-list li { font-size: 13px; line-height: 18px; display: flex; align-items: center; gap: 8px; }
  .contact-list svg { width: 12px; height: 12px; fill: var(--ink); }

  .address { position: absolute; left: 26px; bottom: 18px; font-family: "Open Sans", sans-serif; font-size: 13px; color: var(--address-ink); }
</style>
</head>
<body>
<main class="stage">

  <section class="card card--front" aria-label="Card front">
    <svg class="art" viewBox="0 0 540 310" role="img" aria-label="Decorative green illustration area">
      <defs>
        <linearGradient id="front-fill" x1="0" y1="1" x2="1" y2="0">
          <stop offset="0" stop-color="var(--green-light)"/>
          <stop offset="0.5" stop-color="var(--green-mid)"/>
          <stop offset="1" stop-color="var(--green-dark)"/>
        </linearGradient>
      </defs>
      <polygon points="290,310 540,0 540,310" fill="url(#front-fill)"/>
    </svg>
    <div class="front-brand">
      <div class="brand-name">BRIGHTLINE RETROFIT CO.</div>
      <div class="brand-rule"></div>
      <div class="front-url">www.brightlineretrofit.com</div>
    </div>
  </section>

  <section class="card card--back" aria-label="Card back">
    <svg class="art" viewBox="0 0 540 310" role="img" aria-label="Decorative green illustration area">
      <defs>
        <linearGradient id="back-fill" x1="0" y1="1" x2="1" y2="0">
          <stop offset="0" stop-color="var(--green-light)"/>
          <stop offset="0.6" stop-color="var(--green-mid)"/>
          <stop offset="1" stop-color="var(--green-dark)"/>
        </linearGradient>
      </defs>
      <rect x="0" y="258" width="540" height="52" fill="var(--green-light)"/>
      <polygon points="410,258 540,70 540,258" fill="url(#back-fill)"/>
    </svg>
    <div class="person">
      <div class="person-name">DANIEL REYES</div>
      <div class="person-title">CEO/FOUNDER</div>
    </div>
    <div class="back-brand">
      <div class="brand-name">BRIGHTLINE RETROFIT CO.<span class="brand-mark"></span></div>
      <div class="brand-rule"></div>
    </div>
    <div class="contact">
      <div class="contact-web">www.brightlineretrofit.com</div>
      <div class="contact-web">daniel@brightlineretrofit.com</div>
      <ul class="contact-list">
        <li><svg viewBox="0 0 12 12"><path d="M2 1l2 0 1 3-1.5 1a6 6 0 0 0 3.5 3.5L8 7l3 1v2l-1 1C5 11 1 7 1 2z"/></svg>555 210 4471</li>
        <li><svg viewBox="0 0 12 12"><path d="M3 0h6v12H3zM4 1v8h4V1z"/></svg>555 318 0926</li>
        <li><svg viewBox="0 0 12 12"><path d="M3 1h6v3h2v7H1V4h2zM4 2v2h4V2zM3 6v1h6V6z"/></svg>555 742 3385</li>
      </ul>
    </div>
    <div class="address">214 Harbor Street, Juneau, Alaska 99801</div>
  </section>

</main>
</body>
</html>
```